Business Recognition Design

We need a design for a recognition to be given to business leaders in our community.
The recognition shall be made on a brass plaque on wood panel background (picture attached, please use it as a background), and all drawing must be in vectors and only one color (black).
It should also have a logo on the top and signature on the right bottom.
The text is enclosed in DOC file.
Updates

Reason: just to be able to find the best solution

Reason: None of the suggestion is good enough. Logo in general is too big in comparison with the rest of the plate.

Industry/Entity Type

Business

Requirements
Must have
• - standard Windows font (or possibility to install the same font on Windows), as the name on the recognition shall be printed in the same font
Nice to have
• - some graphic element (in curves) representing achievements in business
- should look great :)

```html
<!DOCTYPE html>
<html lang="en">
<head>
<meta charset="utf-8">
<title>Business Recognition Plaque</title>
<link rel="stylesheet" href="https://fonts.googleapis.com/css2?family=Russo+One&family=Saira:wght@400;500;800&display=swap">
<style>
  :root {
    --wood-dark: #5a351c;
    --wood-mid: #8a5a35;
    --wood-light: #a26f46;
    --gold-deep: #c49a22;
    --gold-mid: #e3c24c;
    --gold-light: #f7e58a;
    --ink: #111008;
    --border-tone: #3b2e0c;
    --flame-1: rgba(232, 120, 60, 0.55);
    --flame-2: rgba(240, 170, 70, 0.25);
  }
  * { margin: 0; padding: 0; box-sizing: border-box; }
  html, body { width: 1200px; height: 924px; overflow: hidden; background: #fff; }
  .plaque {
    position: relative;
    width: 1200px;
    height: 924px;
    background: linear-gradient(135deg, var(--wood-mid), var(--wood-light) 45%, var(--wood-dark));
    font-family: "Saira", "Verdana", sans-serif;
    color: var(--ink);
  }
  .plate {
    position: absolute;
    left: 50px; top: 52px; width: 1100px; height: 823px;
    background:
      repeating-linear-gradient(0deg, rgba(255,255,255,0.06) 0 1px, rgba(0,0,0,0.03) 1px 3px),
      linear-gradient(100deg, var(--gold-deep) 0%, var(--gold-mid) 30%, var(--gold-light) 65%, var(--gold-mid) 85%, var(--gold-deep) 100%);
    border: 2px solid var(--ink);
    box-shadow: inset 0 0 0 4px var(--gold-mid), inset 0 0 0 5px var(--ink);
  }
  .border-band { position: absolute; left: 0; top: 0; width: 1100px; height: 823px; }
  .accent-art {
    position: absolute;
    left: 820px; top: 185px; width: 230px; height: 460px;
    background: radial-gradient(ellipse at 50% 50%, var(--flame-1), var(--flame-2) 55%, transparent 75%);
  }
  .logo-name {
    position: absolute; left: 78px; top: 88px;
    font-family: "Russo One", "Arial Black", sans-serif;
    font-size: 86px; line-height: 1; letter-spacing: 1px;
  }
  .award-title {
    position: absolute; left: 76px; top: 250px; width: 474px; height: 98px;
    border: 4px solid var(--ink); border-radius: 30px;
    display: flex; align-items: center; justify-content: center;
    font-size: 58px; font-weight: 400; letter-spacing: 1px;
  }
  .award-line { position: absolute; left: 76px; font-size: 36px; line-height: 1; letter-spacing: 1px; white-space: nowrap; }
  .award-line.category { top: 398px; }
  .award-line.recipient { top: 454px; }
  .recipient-name { font-weight: 800; }
  .citation {
    position: absolute; left: 76px; top: 538px;
    font-size: 25px; line-height: 42px; letter-spacing: 0.8px; font-weight: 500;
  }
  .company-name { font-weight: 800; }
  .footer-line { position: absolute; top: 722px; font-size: 26px; letter-spacing: 1px; font-weight: 500; }
  .date { left: 76px; }
  .date sup { font-size: 13px; vertical-align: 11px; }
  .signatory { left: 595px; }
</style>
</head>
<body>
<main class="plaque">
  <section class="plate">
    <svg class="border-band" viewBox="0 0 1100 823" role="img" aria-label="Ornamental floral border around the plate">
      <path fill="var(--border-tone)" fill-rule="evenodd" opacity="0.85"
        d="M12 12 H1088 V811 H12 Z M52 52 V771 H1048 V52 Z"/>
      <rect x="8" y="8" width="1084" height="807" fill="none" stroke="var(--ink)" stroke-width="1.5"/>
      <rect x="56" y="56" width="988" height="711" fill="none" stroke="var(--ink)" stroke-width="1"/>
    </svg>

    <div class="accent-art" role="img" aria-label="Faint painted phoenix illustration symbolising business achievement"></div>

    <div class="logo-name">(Our Logo)</div>

    <div class="award-title">RECOGNITION</div>

    <p class="award-line category">The Best Entrepreneur in 2013</p>
    <p class="award-line recipient">to Mr. <span class="recipient-name">Daniel R. Whitfield</span>, MBA</p>

    <p class="citation">
      Under the leadership of Mr. Daniel R. Whitfield, MBA<br>
      the company <span class="company-name">DR-WHITFIELD Ltd</span> has been selected<br>
      by a City Council as the best company of The City.
    </p>

    <p class="footer-line date">Date: 4<sup>th</sup> July, 2013</p>
    <p class="footer-line signatory">City Mayor</p>
  </section>
</main>
</body>
</html>
```